Building company needs a letterhead design

I'm after a modern but professional letter head.
Must have the below details:
- Logo
- Website - TARVELLGROUP.COM.AU
- Email - INFO@TARVELLGROUP.COM.AU
- Office - 03 57263018
- Mobile number - 0418536294
- ABN - 47 315 962 108
...........................................................................................................................................................................................................................
- Logo
- Office - 03 57263018
- ABN - 47 315 962 108

Target Market(s)

.

Industry/Entity Type

Construction Company

Font styles to use
Sans Serif

Requirements
Must have
• Must have the below details:
• - Logo
• - Website - TARVELLGROUP.COM.AU
• - Email - INFO@TARVELLGROUP.COM.AU
• - Office - 03 57263018
• - Mobile number - 0418536294
• - ABN - 47 315 962 108
Nice to have
• .
Should not have
• .

```html
<!DOCTYPE html>
<html lang="en">
<head>
<meta charset="utf-8">
<title>Tarvell Building Group Letterhead</title>
<link rel="stylesheet" href="https://fonts.googleapis.com/css2?family=Open+Sans:wght@400;700&display=swap">
<style>
  :root {
    --gold: #eaa800;
    --charcoal: #4a4848;
    --ink: #3a3a3a;
    --paper: #ffffff;
    --backdrop: #ededed;
  }
  * { margin: 0; padding: 0; box-sizing: border-box; }
  html, body { width: 1200px; height: 1192px; overflow: hidden; background: var(--backdrop); }
  body { font-family: "Open Sans", Arial, sans-serif; position: relative; }
  .letterhead {
    position: absolute; left: 211px; top: 46px;
    width: 778px; height: 1100px;
    background: var(--paper);
    box-shadow: 0 2px 10px rgba(0,0,0,0.12);
    overflow: hidden;
  }
  .swoosh { position: absolute; display: block; }
  .swoosh--top { right: 0; top: 0; }
  .swoosh--bottom { left: 0; bottom: 0; }
  .brand {
    position: absolute; left: 56px; top: 52px;
    display: flex; align-items: center; gap: 12px;
  }
  .brand__mark { width: 30px; height: 30px; background: var(--gold); }
  .brand__name {
    font-weight: 700; font-size: 22px; letter-spacing: 1px;
    color: var(--gold); text-transform: uppercase; line-height: 1.1;
  }
  .contact {
    position: absolute; left: 470px; bottom: 70px;
    font-size: 12px; line-height: 18px; color: var(--ink);
    list-style: none;
  }
  .contact li { display: flex; align-items: center; gap: 8px; }
  .contact__icon { width: 11px; height: 11px; flex: none; }
  .contact__label { color: var(--gold); }
</style>
</head>
<body>
  <main class="letterhead">
    <svg class="swoosh swoosh--top" width="420" height="230" viewBox="0 0 420 230" aria-hidden="true">
      <path d="M0 0 L420 0 L420 215 C330 120 190 45 0 0 Z" fill="var(--gold)"/>
      <path d="M90 30 C230 70 350 140 420 200 L420 230 C340 150 220 80 90 30 Z" fill="var(--charcoal)"/>
      <path d="M90 30 C230 70 350 140 420 200 L420 190 C340 120 220 60 90 30 Z" fill="#fff"/>
    </svg>

    <svg class="swoosh swoosh--bottom" width="470" height="300" viewBox="0 0 470 300" aria-hidden="true">
      <path d="M0 0 C120 110 280 200 400 260 C250 215 110 160 0 120 Z" fill="var(--charcoal)"/>
      <path d="M0 40 C150 160 310 240 470 300 L0 300 Z" fill="var(--gold)"/>
      <path d="M0 30 C150 150 310 232 470 300 L470 296 C310 236 150 156 0 40 Z" fill="#fff"/>
    </svg>

    <header class="brand">
      <span class="brand__mark" aria-hidden="true"></span>
      <span class="brand__name">Tarvell<br>Building Group</span>
    </header>

    <ul class="contact">
      <li>
        <svg class="contact__icon" viewBox="0 0 12 12" aria-hidden="true"><path d="M3 1 L5 3 L4 5 Q5 7 7 8 L9 7 L11 9 L9.5 11 Q3 10 1 2.5 Z" fill="var(--gold)"/></svg>
        <span>03 57263018</span>
      </li>
      <li>
        <svg class="contact__icon" viewBox="0 0 12 12" aria-hidden="true"><rect x="3" y="0.5" width="6" height="11" rx="1" fill="var(--gold)"/><rect x="4" y="2" width="4" height="7" fill="#fff"/></svg>
        <span>0418536294</span>
      </li>
      <li>
        <svg class="contact__icon" viewBox="0 0 12 12" aria-hidden="true"><rect x="0.5" y="2" width="11" height="8" fill="var(--gold)"/><path d="M1 3 L6 7 L11 3" stroke="#fff" fill="none"/></svg>
        <span>info@tarvellgroup.com.au</span>
      </li>
      <li>
        <svg class="contact__icon" viewBox="0 0 12 12" aria-hidden="true"><circle cx="6" cy="6" r="5.5" fill="var(--gold)"/><path d="M0.5 6 H11.5 M6 0.5 Q3 6 6 11.5 Q9 6 6 0.5" stroke="#fff" fill="none"/></svg>
        <span>www.tarvellgroup.com.au</span>
      </li>
      <li><span><span class="contact__label">ABN</span> : 47 315 962 108</span></li>
    </ul>
  </main>
</body>
</html>
```